Briefpapier und Visitenkarten für Bayerisches Gasthaus mit Zimmer
Zielgruppe
Traditionelle Gaststätte im Zentrum einer Kleinstadt in Bayern. Direkt am Marktplatz. 10 Gästezimmer.
Bayerisch. Traditionell. Von junger Geschäftsführerin geführt, mit jungem Personal. Wir haben das Objekt erst vor Kurzem erworben und fangen gerade an.
Gerichte: Braten, Steaks, Brotzeiten, vegetarische und VEGANE Speisen
Getränke: Sehr bierlastig. Es war früher ein Brauereigasthaus. Heute gibts auch eine kleine feine Weinkarte.
Zielgruppe sind Einheimische und Touristen. Im Sommer kommen Radfahrer und Wanderer. Besonders angesprochen werden auch Kinder. Es gibt eine großzügige Spielecke.
Aufgabenstellung
Das Gasthaus heißt Falke. Daher spielt der Falke im Design auch eine wichtige Rolle.
Nachdem wir sehr familienorientiert sind, könnte ich mir auch eine Falke-Familie vorstellen.
Visitenkarten und Briefpapier sollen alle wichtigen Infos enthalten, aber dabei sehr klar gehalten werden und nicht überladen sein. Mir ist ein schlichtes und ansprechendes Design wichtig. Es soll nicht verspielt sein.
Hier ist die Homepage:
www.falke-haldenau-gast.de
Info auf Briefpapier:
GASTHAUS FALKE
Trauber GmbH
Als Info auf Visitenkarte:
Gasthaus Falke

```html
<!DOCTYPE html>
<html lang="de">
<head>
<meta charset="utf-8">
<title>Briefpapier – Gasthaus Falke</title>
<link rel="stylesheet" href="https://fonts.googleapis.com/css2?family=Fira+Sans:wght@300;400&display=swap">
<style>
  :root {
    --green: #a5c520;
    --green-faint: #f5f8ec;
    --text: #4a4a4a;
    --brand-grey: #707070;
    --paper: #ffffff;
  }
  * { margin: 0; padding: 0; box-sizing: border-box; }
  html, body { width: 900px; height: 1200px; overflow: hidden; background: var(--paper); }
  body { font-family: "Fira Sans", sans-serif; font-weight: 300; color: var(--text); }

  .letterhead { position: relative; width: 900px; height: 1200px; background: var(--paper); overflow: hidden; }
  .band { position: absolute; left: 0; width: 900px; height: 11px; background: var(--green); }
  .band--top { top: 0; }
  .band--bottom { bottom: 0; }

  .background-motif {
    position: absolute; left: 0; top: 360px; width: 900px; height: 817px;
    background: radial-gradient(ellipse 70% 60% at 60% 55%, var(--green-faint) 0%, var(--green-faint) 55%, rgba(245,248,236,0) 100%);
  }

  .brand { position: absolute; top: 44px; left: 606px; display: flex; align-items: center; gap: 16px; }
  .brand__dot { width: 52px; height: 52px; border-radius: 50%; background: var(--green); }
  .brand__name { font-size: 29px; line-height: 28px; letter-spacing: 1.5px; color: var(--brand-grey); font-weight: 300; }

  .sender-line { position: absolute; top: 201px; left: 107px; font-size: 7.6px; letter-spacing: 0.1px; }

  .contact { position: absolute; top: 198px; left: 685px; width: 215px; font-size: 11.5px; line-height: 15.5px; }
  .contact__row { display: flex; align-items: center; gap: 6px; }
  .contact__icon { width: 12px; height: 12px; flex: none; }
  .contact__address { padding-left: 18px; margin: 5px 0 5px; }
  .contact__row + .contact__row { margin-top: 4px; }
  .contact__rule { margin-top: 6px; height: 1px; background: var(--green); width: 215px; }

  .fold-mark { position: absolute; left: 0; width: 21px; height: 1px; background: var(--green); }

  .footer { position: absolute; top: 1136px; left: 54px; right: 40px; display: flex; align-items: flex-start; font-size: 10.8px; line-height: 16px; }
  .footer__mark { width: 30px; height: 30px; border-radius: 50%; background: var(--green); margin-right: 23px; margin-top: 2px; flex: none; }
  .footer__col { flex: none; }
</style>
</head>
<body>
<main class="letterhead">
  <div class="band band--top"></div>

  <div class="background-motif" role="img" aria-label="Große, sehr blasse Schmuckfläche mit dem Wappentier des Gasthauses"></div>

  <header class="brand">
    <div class="brand__dot"></div>
    <div class="brand__name">GASTHAUS<br>FALKE</div>
  </header>

  <p class="sender-line">GASTHAUS FALKE ◆ Trauber GmbH ◆ Marktplatz 7 ◆ 93410 Haldenau</p>

  <address class="contact" style="font-style:normal">
    <div class="contact__row">
      <svg class="contact__icon" viewBox="0 0 12 12"><path d="M6 0.5a4 4 0 0 0-4 4c0 3 4 7 4 7s4-4 4-7a4 4 0 0 0-4-4z" fill="var(--green)"/><circle cx="6" cy="4.5" r="1.5" fill="#fff"/></svg>
      <span>GASTHAUS FALKE</span>
    </div>
    <div class="contact__address">Trauber GmbH<br>Marktplatz 7<br>93410 Haldenau</div>
    <div class="contact__row">
      <svg class="contact__icon" viewBox="0 0 12 12"><path d="M3 1l2 2.5-1.2 1.3c.6 1.4 1.8 2.6 3.2 3.2L8.3 6.8 11 9l-1.4 2C5.5 10.6 1.5 6.5 1 2.5z" fill="var(--green)"/></svg>
      <span>09471 3850</span>
    </div>
    <div class="contact__row">
      <svg class="contact__icon" viewBox="0 0 12 12"><circle cx="6" cy="6" r="2" fill="none" stroke="var(--green)" stroke-width="1.5"/><path d="M8 4v3c0 1.5 2.5 1.5 2.5-1A4.5 4.5 0 1 0 8 10" fill="none" stroke="var(--green)" stroke-width="1.5"/></svg>
      <span>info@falke-haldenau-gast.de</span>
    </div>
    <div class="contact__row">
      <svg class="contact__icon" viewBox="0 0 12 12"><circle cx="6" cy="6" r="5" fill="none" stroke="var(--green)" stroke-width="1.3"/><path d="M1 6h10M6 1c-2.5 3-2.5 7 0 10M6 1c2.5 3 2.5 7 0 10" fill="none" stroke="var(--green)" stroke-width="1"/></svg>
      <span>www.falke-haldenau-gast.de</span>
    </div>
    <div class="contact__rule"></div>
  </address>

  <div class="fold-mark" style="top:424px"></div>
  <div class="fold-mark" style="top:599px"></div>
  <div class="fold-mark" style="top:848px"></div>

  <footer class="footer">
    <div class="footer__mark"></div>
    <div class="footer__col" style="width:116px">Steuernummer:<br>USt.-IdNr. DE xxx</div>
    <div class="footer__col" style="width:112px">Handelsregister:<br>ORT</div>
    <div class="footer__col" style="width:133px">Geschäftsführer:<br>Vorname Nachname</div>
    <div class="footer__col" style="width:87px">Bank:<br>Musterbank</div>
    <div class="footer__col" style="width:212px">IBAN DExx xxxx xxxx xxxx xxxx xx<br>BIC XXXXXXX 1XXX</div>
    <div class="footer__col">Kontoinhaber:<br>Trauber GmbH</div>
  </footer>

  <div class="band band--bottom"></div>
</main>
</body>
</html>
```